TA BRAMLEY BUSINESS CARD DESIGN PROJECT

We need to utilize our logo that was expertly created on PixelHarbor and now need to match this with a business card design.

```html
<!DOCTYPE html>
<html lang="en">
<head>
<meta charset="utf-8">
<title>TA BRAMLEY – Business Card</title>
<link rel="stylesheet" href="https://fonts.googleapis.com/css2?family=Montserrat:wght@400;500;700;800&display=swap">
<style>
  :root {
    --backdrop: #474747;
    --card-black: #161616;
    --brand-blue: #0f57a8;
    --text-white: #f2f2f2;
    --emboss: #2b2b2b;
  }
  * { margin: 0; padding: 0; box-sizing: border-box; }
  html, body {
    width: 1200px; height: 801px; overflow: hidden;
    background: var(--backdrop);
    font-family: "Montserrat", sans-serif;
  }
  .stage { position: relative; width: 1200px; height: 801px; }
  .card {
    position: absolute; top: 246px;
    width: 540px; height: 309px;
    background: var(--card-black);
    overflow: hidden;
  }
  .card--front { left: 40px; }
  .card--back { left: 620px; }
  .card__wave { position: absolute; inset: 0; }
  .brand-name {
    position: absolute; left: 50px; top: 132px; width: 240px;
    text-align: center;
    font-weight: 800; font-size: 27px; letter-spacing: 1px;
    color: var(--brand-blue);
  }
  .divider {
    position: absolute; left: 314px; top: 62px;
    width: 1.5px; height: 160px;
    background: var(--brand-blue);
  }
  .contact {
    position: absolute; left: 332px; top: 58px;
    color: var(--text-white); font-size: 11px; line-height: 15px;
  }
  .contact__name {
    font-weight: 700; font-size: 15px; color: var(--brand-blue);
    letter-spacing: .5px; line-height: 18px;
  }
  .contact__title { font-size: 12px; margin-bottom: 10px; }
  .contact__row { display: flex; align-items: center; gap: 6px; }
  .contact__icon { width: 9px; height: 9px; flex: none; }
  .contact__address { margin-top: 10px; }
  .back-name {
    position: absolute; inset: 0;
    display: flex; align-items: center; justify-content: center;
    font-weight: 800; font-size: 54px; letter-spacing: 3px;
    color: var(--emboss);
  }
</style>
</head>
<body>
<main class="stage">
  <section class="card card--front" aria-label="Business card front">
    <svg class="card__wave" viewBox="0 0 540 309" aria-hidden="true">
      <path d="M0,210 C60,242 130,272 210,272 C310,272 420,258 540,262 L540,309 L0,309 Z" fill="var(--brand-blue)"/>
      <path d="M84,256 C150,262 230,258 300,250 C390,241 470,240 540,246" fill="none" stroke="var(--brand-blue)" stroke-width="3"/>
    </svg>
    <div class="brand-name">TA BRAMLEY</div>
    <div class="divider"></div>
    <div class="contact">
      <div class="contact__name">MARCUS HALE</div>
      <div class="contact__title">Managing Director</div>
      <div class="contact__row">
        <svg class="contact__icon" viewBox="0 0 10 10"><path d="M2 1 L4 1 L4.6 3 L3.4 4 C4 5.4 4.8 6.2 6 6.6 L7 5.4 L9 6 L9 8 C5 9 1 5 2 1 Z" fill="var(--brand-blue)"/></svg>
        <span>123 456 789</span>
      </div>
      <div class="contact__row">
        <svg class="contact__icon" viewBox="0 0 10 10"><rect x="1.5" y="1" width="7" height="8" rx="1" fill="var(--brand-blue)"/></svg>
        <span>123 456 789</span>
      </div>
      <div class="contact__row">
        <svg class="contact__icon" viewBox="0 0 10 10"><rect x="1" y="2.5" width="8" height="5.5" fill="var(--brand-blue)"/><path d="M1 2.5 L5 5.5 L9 2.5" fill="none" stroke="var(--card-black)" stroke-width=".8"/></svg>
        <span>info@yourgmail.com</span>
      </div>
      <div class="contact__row">
        <svg class="contact__icon" viewBox="0 0 10 10"><circle cx="5" cy="5" r="4" fill="var(--brand-blue)"/></svg>
        <span>www.yourwebsite.com</span>
      </div>
      <div class="contact__address">Your address, City<br>State, Zip 1234</div>
    </div>
  </section>

  <section class="card card--back" aria-label="Business card back">
    <div class="back-name">TA BRAMLEY</div>
  </section>
</main>
</body>
</html>
```